Business Card Design Project

use presentation folder design and my logo and make 4 over 4 business cards

Industry/Entity Type

Business

Requirements
Must have
• use the design from my presentation folder and put my logo on it

Name
Title
phone
fax
email

```html
<!DOCTYPE html>
<html lang="en">
<head>
<meta charset="utf-8">
<title>BrightPath Counseling – Business Cards</title>
<link rel="stylesheet" href="https://fonts.googleapis.com/css2?family=Tinos&family=Questrial&display=swap">
<style>
  :root {
    --page: #fcfafb;
    --card: #ffffff;
    --grey-light: #c4c4c4;
    --grey-dark: #858585;
    --grey-text: #7d7d7d;
    --brown: #7e4620;
    --brown-light: #a0683a;
    --brown-text: #8a4b1c;
    --mist: #f2f2f2;
  }
  * { margin: 0; padding: 0; box-sizing: border-box; }
  html, body {
    width: 1200px; height: 1000px; overflow: hidden;
    background: var(--page);
  }
  .sheet { position: relative; width: 1200px; height: 1000px; }
  .card {
    position: absolute; left: 205px; width: 787px; height: 438px;
    background: var(--card); overflow: hidden;
  }
  .card--front { top: 43px; }
  .card--back { top: 522px; }

  .decor { position: absolute; }
  .decor--grey { background: linear-gradient(135deg, var(--grey-dark), var(--grey-light) 55%, var(--grey-dark)); }
  .decor--brown { background: linear-gradient(200deg, var(--brown-light), var(--brown) 45%, #8f5424); }
  .decor--mist { background: linear-gradient(180deg, var(--mist), #f7f7f7); }

  .card--front .decor--grey { left: 0; top: 0; width: 96px; height: 100%; }
  .card--front .decor--brown { right: 0; top: 0; width: 120px; height: 100%; }

  .card--back .decor--grey { left: 0; top: 0; width: 58px; height: 100%; }
  .card--back .decor--brown {
    left: 90px; top: 0; width: 600px; height: 360px;
    clip-path: polygon(72% 0, 100% 0, 10% 100%, 0 100%);
  }
  .card--back .decor--mist { right: 0; top: 300px; width: 560px; height: 138px; }

  .wordmark {
    position: absolute; display: flex; align-items: center; gap: 14px;
    font-family: "Tinos", serif; color: var(--brown-text); white-space: nowrap;
  }
  .wordmark__dot { border-radius: 50%; background: var(--grey-dark); flex: none; }
  .wordmark--large { left: 0; right: 0; top: 210px; justify-content: center; font-size: 50px; }
  .wordmark--large .wordmark__dot { width: 34px; height: 34px; }
  .wordmark--small { left: 232px; top: 420px; font-size: 24px; gap: 8px; transform: translateY(-100%); }
  .wordmark--small .wordmark__dot { width: 16px; height: 16px; }

  .person { position: absolute; right: 53px; text-align: right; white-space: nowrap; }
  .person__name {
    top: 208px; font-family: "Tinos", serif; font-size: 45px; color: var(--grey-text);
  }
  .person__name strong { font-weight: 400; color: var(--brown-text); }
  .person__title {
    top: 280px; font-family: "Questrial", sans-serif; font-size: 34px; color: var(--brown-text);
  }

  .divider {
    position: absolute; left: 446px; top: 358px; width: 1px; height: 80px;
    background: var(--brown-light);
  }
  .contact {
    position: absolute; left: 467px; top: 354px; list-style: none;
    font-family: "Questrial", sans-serif; font-size: 20px; line-height: 29px;
    color: var(--brown-light); white-space: nowrap;
  }
</style>
</head>
<body>
<main class="sheet">

  <section class="card card--front" aria-label="Card front">
    <div class="decor decor--grey" role="img" aria-label="Grey decorative band"></div>
    <div class="decor decor--brown" role="img" aria-label="Brown decorative band"></div>
    <div class="wordmark wordmark--large"><span class="wordmark__dot"></span>BrightPath Counseling</div>
  </section>

  <section class="card card--back" aria-label="Card back">
    <div class="decor decor--mist" role="img" aria-label="Pale grey decorative area"></div>
    <div class="decor decor--grey" role="img" aria-label="Grey decorative band"></div>
    <div class="decor decor--brown" role="img" aria-label="Brown diagonal decorative band"></div>

    <p class="person person__name">Name <strong>Surname</strong></p>
    <p class="person person__title">Job Title</p>

    <div class="wordmark wordmark--small"><span class="wordmark__dot"></span>BrightPath</div>
    <span class="divider"></span>
    <ul class="contact">
      <li>Phone:</li>
      <li>Fax:</li>
      <li>xxx.xxx.xxx@brightpath.com</li>
    </ul>
  </section>

</main>
</body>
</html>
```